Building company buisness cards

We are looking for a sharp modern new look for our business cards.We are a New Zealand based company that specialises in house and land packages.We have attached a photo of the current logo and would like to see if it can be improved somehow if needed.We are open to any colours but we have chosen Black and White at this stage. Feel free to change the font and make the logo smarter looking.Play with the colours and see what looks best.We want a card that looks so good know one will want to throw it away!

Target Market(s)

Building profesonals, home buyers

Industry/Entity Type

Building

Contact Information for Business Card

Garrick Tenwood
0275390628
garrickt@hartvale.co.nz

Font styles to use
Serif
Sans Serif

Colors

Designer to choose colors to be used in the design.

Requirements
Must have
• Just the logo on one side and details on the other
• Clean simple looking card
Nice to have
• Round corners and detail like raised or spot UV
• Something that stands out
Should not have
• To title needed, Director etc

```html
<!DOCTYPE html>
<html lang="en">
<head>
<meta charset="utf-8">
<title>Hartvale Business Cards</title>
<link rel="stylesheet" href="https://fonts.googleapis.com/css2?family=Roboto:wght@400;500;700&display=swap">
<style>
  :root {
    --navy: #1d2858;
    --orange: #f0961e;
    --paper: #d8d8d8;
    --white: #ffffff;
    --text-grey: #555a60;
    --rule-grey: #cfcfcf;
  }
  * { box-sizing: border-box; margin: 0; padding: 0; }
  html, body {
    width: 1125px;
    height: 1200px;
    overflow: hidden;
    background: var(--paper);
  }
  .canvas {
    position: relative;
    width: 1125px;
    height: 1200px;
  }
  .card {
    position: absolute;
    left: 156px;
    width: 825px;
    height: 471px;
    border-radius: 24px;
    overflow: hidden;
  }
  .card-front { top: 106px; background: var(--white); }
  .card-back { top: 639px; background: var(--navy); }

  .brand-name {
    font-family: 'Roboto', sans-serif;
    font-weight: 700;
    line-height: 1;
    white-space: nowrap;
  }
  .front-brand {
    position: absolute;
    right: 415px;
    top: 237px;
    transform: translateY(-50%);
    font-size: 50px;
    color: var(--navy);
  }
  .divider {
    position: absolute;
    left: 444px;
    top: 154px;
    width: 1px;
    height: 166px;
    background: var(--rule-grey);
  }
  .details {
    position: absolute;
    left: 482px;
    top: 160px;
    font-family: 'Roboto', sans-serif;
  }
  .person-name {
    font-weight: 700;
    font-size: 28px;
    color: var(--navy);
    margin-bottom: 20px;
  }
  .contact-list { list-style: none; }
  .contact-item {
    display: flex;
    align-items: center;
    gap: 12px;
    font-size: 19px;
    color: var(--text-grey);
    height: 26px;
  }
  .contact-item svg { width: 18px; height: 18px; fill: var(--navy); flex: none; }

  .band-accent {
    position: absolute;
    left: 0; right: 0;
    top: 444px;
    height: 3px;
    background: var(--orange);
  }
  .band-base {
    position: absolute;
    left: 0; right: 0;
    top: 447px;
    bottom: 0;
    background: var(--navy);
  }

  .back-brand {
    position: absolute;
    left: 0; right: 0;
    top: 235px;
    transform: translateY(-50%);
    text-align: center;
    font-size: 60px;
    color: var(--white);
  }
  .back-url {
    position: absolute;
    left: 0; right: 0;
    top: 402px;
    text-align: center;
    font-family: 'Roboto', sans-serif;
    font-size: 19px;
    letter-spacing: 0.55em;
    color: var(--white);
  }
</style>
</head>
<body>
<main class="canvas">
  <section class="card card-front">
    <p class="brand-name front-brand">Hartvale</p>
    <div class="divider"></div>
    <div class="details">
      <h1 class="person-name">Garrick Tenwood</h1>
      <ul class="contact-list">
        <li class="contact-item">
          <svg viewBox="0 0 24 24" aria-hidden="true"><path d="M6.6 10.8a15.1 15.1 0 0 0 6.6 6.6l2.2-2.2a1 1 0 0 1 1-.25 11.4 11.4 0 0 0 3.6.57 1 1 0 0 1 1 1V20a1 1 0 0 1-1 1A17 17 0 0 1 3 4a1 1 0 0 1 1-1h3.5a1 1 0 0 1 1 1c0 1.25.2 2.45.57 3.57a1 1 0 0 1-.25 1z"/></svg>
          0275390628
        </li>
        <li class="contact-item">
          <svg viewBox="0 0 24 24" aria-hidden="true"><path d="M2 5h20v14H2z M4 7v.4l8 5.2 8-5.2V7z" fill-rule="evenodd"/></svg>
          garrickt@hartvale.co.nz
        </li>
        <li class="contact-item">
          <svg viewBox="0 0 24 24" aria-hidden="true"><path d="M12 2a10 10 0 1 0 0 20 10 10 0 0 0 0-20zm-1 17.9A8 8 0 0 1 4.1 10L9 15v1a2 2 0 0 0 2 2zm6.9-2.5A2 2 0 0 0 16 16h-1v-3a1 1 0 0 0-1-1H8v-2h2a1 1 0 0 0 1-1V7h2a2 2 0 0 0 2-2v-.4a8 8 0 0 1 2.9 12.8z"/></svg>
          www.hartvale.co.nz
        </li>
      </ul>
    </div>
    <div class="band-accent"></div>
    <div class="band-base"></div>
  </section>

  <section class="card card-back">
    <p class="brand-name back-brand">Hartvale</p>
    <p class="back-url">www.Hartvale.co.nz</p>
  </section>
</main>
</body>
</html>
```